Oil and Gas Exploration and Production company needs a business card design

We need a business card design using our logo and colors in the logo. We want a mainstream design.

```html
<!DOCTYPE html>
<html lang="en">
<head>
<meta charset="utf-8">
<title>Vireo Oil &amp; Gas — Business Card</title>
<link rel="stylesheet" href="https://fonts.googleapis.com/css2?family=Work+Sans:wght@400;500;700&display=swap">
<style>
  :root {
    --backdrop: #1e1e1e;
    --card: #141414;
    --card-edge: #0c0c0c;
    --silver: #d9d9d9;
    --silver-soft: #bdbdbd;
    --emboss: #3a3a3a;
    --divider: #8a8a8a;
  }
  * { margin: 0; padding: 0; box-sizing: border-box; }
  html, body {
    width: 1200px; height: 900px; overflow: hidden;
    background: var(--backdrop);
    font-family: "Work Sans", sans-serif;
  }
  .canvas {
    position: relative; width: 1200px; height: 900px;
    display: flex; flex-direction: column; align-items: center;
    justify-content: center; gap: 24px;
  }
  .card {
    width: 700px; height: 400px;
    background: var(--card);
    border: 1px solid var(--card-edge);
    position: relative;
  }
  .wordmark {
    display: flex; align-items: center; gap: 14px;
    font-weight: 700; letter-spacing: 0.5px;
  }
  .wordmark-dot {
    width: 22px; height: 22px; border-radius: 50%;
  }
  .card-front {
    display: flex; align-items: center; justify-content: center;
  }
  .card-front .wordmark { color: var(--silver-soft); font-size: 54px; }
  .card-front .wordmark-dot { background: var(--silver-soft); }

  .card-back { display: flex; align-items: center; }
  .card-back .brand-side {
    width: 330px; display: flex; justify-content: center;
  }
  .card-back .wordmark { color: var(--emboss); font-size: 38px; }
  .card-back .wordmark-dot { background: var(--emboss); width: 18px; height: 18px; }
  .divider {
    width: 1px; height: 240px; background: var(--divider);
  }
  .contact-side {
    padding-left: 44px; color: var(--silver);
  }
  .person-name { font-size: 30px; font-weight: 500; }
  .person-role { font-size: 14px; color: var(--silver-soft); margin-top: 2px; letter-spacing: 1px; }
  .address { font-size: 16px; line-height: 1.4; margin-top: 22px; letter-spacing: 0.5px; }
  .contact-list { list-style: none; margin-top: 14px; font-size: 17px; letter-spacing: 0.5px; }
  .contact-list li { display: flex; align-items: center; gap: 10px; line-height: 1.55; }
  .contact-list svg { width: 13px; height: 13px; flex: none; }
</style>
</head>
<body>
<main class="canvas">
  <section class="card card-front">
    <div class="wordmark"><span class="wordmark-dot"></span>Vireo Oil &amp; Gas</div>
  </section>

  <section class="card card-back">
    <div class="brand-side">
      <div class="wordmark"><span class="wordmark-dot"></span>Vireo Oil &amp; Gas</div>
    </div>
    <div class="divider"></div>
    <div class="contact-side">
      <p class="person-name">Dale Hartman</p>
      <p class="person-role">CFO</p>
      <p class="address">2450 Meridian Ave,<br>Abilene, Texas US</p>
      <ul class="contact-list">
        <li>
          <svg viewBox="0 0 16 16" fill="none" stroke="#d9d9d9" stroke-width="1.6"><path d="M4 1.5h2.5l1 3.5-1.8 1.2a8 8 0 0 0 4.1 4.1L11 8.5l3.5 1V12a2.5 2.5 0 0 1-2.5 2.5A10.5 10.5 0 0 1 1.5 4 2.5 2.5 0 0 1 4 1.5z"/></svg>
          (555) 014-2276
        </li>
        <li>
          <svg viewBox="0 0 16 16" fill="none" stroke="#d9d9d9" stroke-width="1.6"><rect x="1.5" y="3.5" width="13" height="9"/><path d="M1.5 3.5 8 9l6.5-5.5"/></svg>
          info@vireoenergy.com
        </li>
        <li>
          <svg viewBox="0 0 16 16" fill="none" stroke="#d9d9d9" stroke-width="1.4"><circle cx="8" cy="8" r="6.5"/><ellipse cx="8" cy="8" rx="2.8" ry="6.5"/><path d="M1.5 8h13"/></svg>
          www.vireoenergy.com
        </li>
      </ul>
    </div>
  </section>
</main>
</body>
</html>
```